New menu rebranding for Asian fusion

I have my current menu attached, but I want to change it and make it more attractive. The restaurant is an Asian Fusion. Food from Thailand, China, Japan, Indonesia, Malaysia, Cambodia. We cater to mid to high end consumers with an educated and sophisticated pallet. Maybe try a modern twist, or an authentic variation, maybe a mix. Please don't play with the logo too much, but feel free to play with the pattern. I also want to have as many pictures of dishes visible as possible. Additionally, keep in mind that the menu will be in two languages, so please design accordingly. Feel free to play around with the format of the menu and the logo too if you get carried away. Keep it in mind that this is also a take out menu too. Please check out the Instagram account lotus_crate As well as facebook etc. Let me know if you need any additional files. Thx and appreciated.
Updates

I have made an update to the Menu. It's not the original file. It's smaller now. Please see the attached PDF file. Best regards, Added Monday, February 02, 2015

Target Market(s)

Mid to high end

Industry/Entity Type

Restaurant

Number of Pages Required

3 page

Requirements
Must have
• dual language friendly. At least make space for it.
• Must keep logo.
Nice to have
• Would be nice to stick to same theme, not too much change to branding.

```html
<!DOCTYPE html>
<html lang="en">
<head>
<meta charset="utf-8">
<title>Appetizers Menu Spread</title>
<link rel="stylesheet" href="https://fonts.googleapis.com/css2?family=Michroma&display=swap">
<style>
  :root{
    --orange:#f39019;
    --ink:#1a1a1a;
    --label-border:#1d2427;
    --page-edge:#9a9a9a;
    --sheet:#ffffff;
    --column-grey:#b9b9b9;
  }
  html,body{margin:0;padding:0;width:1200px;height:1000px;overflow:hidden;background:#fff;}
  body{position:relative;font-family:"Michroma",sans-serif;color:var(--ink);}
  .page{position:absolute;top:141px;height:747px;border:1px solid var(--page-edge);box-sizing:border-box;overflow:hidden;background:var(--sheet);}
  .page--left{left:37px;width:562px;}
  .page--right{left:601px;width:563px;}
  .dish-photo{position:absolute;width:256px;height:235px;}
  .page--left .dish-photo{left:0;border-radius:0 18px 18px 0;}
  .page--right .dish-photo{right:0;border-radius:18px 0 0 18px;}
  .photo-1{top:9px;background:radial-gradient(circle at 40% 45%,#7a2a14 0%,#4a1a0f 45%,#2a1410 75%,#d8d6d2 100%);}
  .photo-2{top:254px;background:linear-gradient(180deg,#2b3034 0%,#3b3f40 35%,#c9a646 60%,#e4c24a 80%,#8a7a3a 100%);}
  .photo-3{top:499px;background:radial-gradient(circle at 45% 60%,#e7a582 0%,#8a6a55 35%,#3a3430 70%,#1c1a1a 100%);}
  .dish-label{position:absolute;width:88px;height:88px;box-sizing:border-box;border:5px solid var(--label-border);border-radius:15px;background:var(--orange);color:#fff;font-size:11.5px;line-height:15px;display:flex;align-items:center;justify-content:center;text-align:center;}
  .page--left .dish-label{left:196px;}
  .page--right .dish-label{left:269px;}
  .label-1{top:83px;}
  .label-2{top:327px;}
  .label-3{top:568px;}
  .menu-column{position:absolute;top:0;bottom:0;width:264px;}
  .page--left .menu-column{left:295px;background:linear-gradient(90deg,#ffffff 0%,#efefef 40%,var(--column-grey) 100%);}
  .page--right .menu-column{left:0;width:268px;background:linear-gradient(90deg,var(--column-grey) 0%,#efefef 60%,#ffffff 100%);}
  .menu-head{position:absolute;top:0;left:0;right:0;height:34px;background:var(--orange);display:flex;align-items:center;font-size:10px;}
  .page--left .menu-head{border-radius:0 0 0 16px;}
  .page--right .menu-head{border-radius:0 0 16px 0;}
  .head-no{position:absolute;left:12px;top:12px;}
  .head-title{position:absolute;left:80px;top:8px;font-size:13px;}
  .head-price{position:absolute;right:15px;top:12px;}
  .menu-item{position:absolute;left:0;right:0;}
  .item-no{position:absolute;left:8px;top:3px;font-size:9px;}
  .item-name{position:absolute;left:38px;top:0;color:var(--orange);font-size:11.5px;}
  .item-price{position:absolute;right:16px;top:3px;font-size:9px;}
  .item-desc{position:absolute;left:38px;top:16px;width:190px;margin:0;font-size:8px;line-height:12px;}
</style>
</head>
<body>
  <section class="page page--left">
    <div class="dish-photo photo-1" role="img" aria-label="Photo of Indonesian chicken glazed with sesame and spring onion"></div>
    <div class="dish-photo photo-2" role="img" aria-label="Photo of chicken penang curry with red chili"></div>
    <div class="dish-photo photo-3" role="img" aria-label="Photo of tom yum goung soup with prawns"></div>
    <div class="dish-label label-1">Indonesian<br>Chicken</div>
    <div class="dish-label label-2">Chicken<br>Penang<br>Curry</div>
    <div class="dish-label label-3">Tom Yum<br>Goung</div>
    <div class="menu-column">
      <div class="menu-head"><span class="head-no">No.</span><span class="head-title">Appetizers</span><span class="head-price">SR</span></div>
      <div class="menu-item" style="top:43px"><span class="item-no">101</span><span class="item-name">Chicken Satay</span><span class="item-price">25</span><p class="item-desc">Bar BQ chicken skewers marinated in thai herbs served with sweet tangy peanut sauce</p></div>
      <div class="menu-item" style="top:113px"><span class="item-no">102</span><span class="item-name">Shrimp Satay</span><span class="item-price">30</span><p class="item-desc">Bar BQ shrimp skewers marinated in thai herbs served with sweet tangy peanut sauce</p></div>
      <div class="menu-item" style="top:183px"><span class="item-no">103</span><span class="item-name">Dendeng</span><span class="item-price">38</span><p class="item-desc">Our signature appetizer. crispy beef tossed in an aromatic spicy sauce with fried onions</p></div>
      <div class="menu-item" style="top:263px"><span class="item-no">104</span><span class="item-name">Calamari</span><span class="item-price">28</span><p class="item-desc">Tender calamari lightly dusted and wok fried served with a chili soy dipping sauce</p></div>
      <div class="menu-item" style="top:331px"><span class="item-no">105</span><span class="item-name">Spring Rolls</span><span class="item-price">23</span><p class="item-desc">Crispy fried spring rolls filled with fresh vegetables served with a sweet chilli dipping sauce</p></div>
      <div class="menu-item" style="top:396px"><span class="item-no">106</span><span class="item-name">Chicken Satay</span><span class="item-price">25</span><p class="item-desc">Bar BQ chicken skewers marinated in thai herbs served with sweet tangy peanut sauce</p></div>
      <div class="menu-item" style="top:466px"><span class="item-no">107</span><span class="item-name">Shrimp Satay</span><span class="item-price">30</span><p class="item-desc">Bar BQ shrimp skewers marinated in thai herbs served with sweet tangy peanut sauce</p></div>
      <div class="menu-item" style="top:536px"><span class="item-no">108</span><span class="item-name">Dendeng</span><span class="item-price">38</span><p class="item-desc">Our signature appetizer. crispy beef tossed in an aromatic spicy sauce with fried onions</p></div>
      <div class="menu-item" style="top:615px"><span class="item-no">109</span><span class="item-name">Calamari</span><span class="item-price">28</span><p class="item-desc">Tender calamari lightly dusted and wok fried served with a chili soy dipping sauce</p></div>
      <div class="menu-item" style="top:685px"><span class="item-no">110</span><span class="item-name">Spring Rolls</span><span class="item-price">23</span><p class="item-desc">Crispy fried spring rolls filled with fresh vegetables served with a sweet chilli dipping sauce</p></div>
    </div>
  </section>

  <section class="page page--right">
    <div class="dish-photo photo-1" role="img" aria-label="Photo of Indonesian chicken glazed with sesame and spring onion"></div>
    <div class="dish-photo photo-2" role="img" aria-label="Photo of chicken penang curry with red chili"></div>
    <div class="dish-photo photo-3" role="img" aria-label="Photo of tom yum goung soup with prawns"></div>
    <div class="menu-column">
      <div class="menu-head"><span class="head-no">No.</span><span class="head-title">Appetizers</span><span class="head-price">SR</span></div>
      <div class="menu-item" style="top:43px"><span class="item-no">101</span><span class="item-name">Chicken Satay</span><span class="item-price">25</span><p class="item-desc">Bar BQ chicken skewers marinated in thai herbs served with sweet tangy peanut sauce</p></div>
      <div class="menu-item" style="top:113px"><span class="item-no">102</span><span class="item-name">Shrimp Satay</span><span class="item-price">30</span><p class="item-desc">Bar BQ shrimp skewers marinated in thai herbs served with sweet tangy peanut sauce</p></div>
      <div class="menu-item" style="top:183px"><span class="item-no">103</span><span class="item-name">Dendeng</span><span class="item-price">38</span><p class="item-desc">Our signature appetizer. crispy beef tossed in an aromatic spicy sauce with fried onions</p></div>
      <div class="menu-item" style="top:263px"><span class="item-no">104</span><span class="item-name">Calamari</span><span class="item-price">28</span><p class="item-desc">Tender calamari lightly dusted and wok fried served with a chili soy dipping sauce</p></div>
      <div class="menu-item" style="top:331px"><span class="item-no">105</span><span class="item-name">Spring Rolls</span><span class="item-price">23</span><p class="item-desc">Crispy fried spring rolls filled with fresh vegetables served with a sweet chilli dipping sauce</p></div>
      <div class="menu-item" style="top:396px"><span class="item-no">106</span><span class="item-name">Chicken Satay</span><span class="item-price">25</span><p class="item-desc">Bar BQ chicken skewers marinated in thai herbs served with sweet tangy peanut sauce</p></div>
      <div class="menu-item" style="top:466px"><span class="item-no">107</span><span class="item-name">Shrimp Satay</span><span class="item-price">30</span><p class="item-desc">Bar BQ shrimp skewers marinated in thai herbs served with sweet tangy peanut sauce</p></div>
      <div class="menu-item" style="top:536px"><span class="item-no">108</span><span class="item-name">Dendeng</span><span class="item-price">38</span><p class="item-desc">Our signature appetizer. crispy beef tossed in an aromatic spicy sauce with fried onions</p></div>
      <div class="menu-item" style="top:615px"><span class="item-no">109</span><span class="item-name">Calamari</span><span class="item-price">28</span><p class="item-desc">Tender calamari lightly dusted and wok fried served with a chili soy dipping sauce</p></div>
      <div class="menu-item" style="top:685px"><span class="item-no">110</span><span class="item-name">Spring Rolls</span><span class="item-price">23</span><p class="item-desc">Crispy fried spring rolls filled with fresh vegetables served with a sweet chilli dipping sauce</p></div>
    </div>
    <div class="dish-label label-1">Indonesian<br>Chicken</div>
    <div class="dish-label label-2">Chicken<br>Penang<br>Curry</div>
    <div class="dish-label label-3">Tom Yum<br>Goung</div>
  </section>
</body>
</html>
```